Our companies name is The Gilded Ladle and we specialize in craft cupcakes, what I mean by that is that we bake our cupcakes with craft beer and other alcoholic drinks. We are trying to focus on being elegant but at the same time unpretentious. Since we are incorporating beer in our cupcakes we want the business card to have our logo in the front and our information in the back.

Once we select the best design we will provide the contact information to be added. Thank you.

Industry/Entity Type

Business

Font styles to use
Decorative
Script

Requirements
Must have
• Round corners
Should not have
• Square corners

```html
<!DOCTYPE html>
<html lang="en">
<head>
<meta charset="utf-8">
<title>The Gilded Ladle – Business Card</title>
<link href="https://fonts.googleapis.com/css2?family=Exo+2:wght@400;500;600&display=swap" rel="stylesheet">
<style>
  :root {
    --page-bg: #e9e7e4;
    --card-white: #f7f7f7;
    --card-black: #0c0c0c;
    --accent-orange: #f2561d;
    --text-light: #ffffff;
    --brand-ink: #1c2a2e;
    --brand-dot: #6fc3c0;
  }
  * { margin: 0; padding: 0; box-sizing: border-box; }
  html, body {
    width: 1200px; height: 900px; overflow: hidden;
    background: var(--page-bg);
    font-family: "Exo 2", sans-serif;
  }
  .canvas {
    position: relative; width: 1200px; height: 900px;
    display: flex; align-items: center; justify-content: center;
  }
  .business-card {
    position: relative; width: 1000px; height: 571px;
    border-radius: 56px; overflow: hidden;
    background: var(--card-white);
    box-shadow: 0 18px 40px rgba(0,0,0,0.18);
  }
  .card-shapes { position: absolute; inset: 0; width: 100%; height: 100%; }
  .card-shapes .panel-black { fill: var(--card-black); }
  .card-shapes .swoosh-orange { fill: var(--accent-orange); }

  .brand-mark {
    position: absolute; left: 80px; top: 258px;
    display: flex; align-items: center; gap: 14px;
  }
  .brand-mark .brand-dot {
    width: 34px; height: 34px; border-radius: 50%;
    background: var(--brand-dot);
  }
  .brand-mark .brand-name {
    font-weight: 600; font-size: 34px; color: var(--brand-ink);
    text-transform: uppercase; letter-spacing: 1px; white-space: nowrap;
  }

  .contact-block {
    position: absolute; right: 70px; top: 70px;
    text-align: right; color: var(--text-light);
  }
  .person-name { font-size: 30px; font-weight: 500; letter-spacing: 1.5px; text-transform: uppercase; }
  .person-title { font-size: 19px; letter-spacing: 2px; text-transform: uppercase; margin-top: 4px; }
  .address { font-size: 23px; line-height: 1.25; margin-top: 58px; letter-spacing: 0.5px; }
  .contact-list { list-style: none; margin-top: 38px; }
  .contact-list li {
    font-size: 21px; letter-spacing: 0.8px; line-height: 1;
    display: flex; justify-content: flex-end; align-items: center; gap: 12px;
    height: 38px;
  }
  .contact-list .icon { width: 22px; height: 22px; fill: none; stroke: var(--text-light); stroke-width: 2; }
  .contact-list .icon.solid { fill: var(--text-light); stroke: none; }
  .contact-list .web { gap: 0; }
</style>
</head>
<body>
<main class="canvas">
  <section class="business-card">
    <svg class="card-shapes" viewBox="0 0 1000 571" preserveAspectRatio="none" aria-hidden="true">
      <path class="swoosh-orange" d="M255,0 C500,25 610,280 545,571 L560,571 C625,300 560,60 345,0 Z"/>
      <path class="panel-black" d="M345,0 C560,60 625,300 560,571 L1000,571 L1000,0 Z"/>
    </svg>

    <div class="brand-mark">
      <span class="brand-dot"></span>
      <span class="brand-name">The Gilded Ladle</span>
    </div>

    <div class="contact-block">
      <p class="person-name">Dana Whitfield</p>
      <p class="person-title">President</p>
      <p class="address">214,3rd floor,Mill<br>Harbour Lane CRK</p>
      <ul class="contact-list">
        <li>012 555 0147
          <svg class="icon solid" viewBox="0 0 24 24"><path d="M6.6 10.8a15 15 0 0 0 6.6 6.6l2.2-2.2a1 1 0 0 1 1-.25 11.4 11.4 0 0 0 3.6.57 1 1 0 0 1 1 1V20a1 1 0 0 1-1 1A17 17 0 0 1 3 4a1 1 0 0 1 1-1h3.5a1 1 0 0 1 1 1c0 1.25.2 2.45.57 3.57a1 1 0 0 1-.25 1z"/></svg>
        </li>
        <li>012 555 0147
          <svg class="icon" viewBox="0 0 24 24"><rect x="6" y="2" width="12" height="20" rx="2"/><line x1="10" y1="18.5" x2="14" y2="18.5"/></svg>
        </li>
        <li>012 555 0147
          <svg class="icon" viewBox="0 0 24 24"><rect x="4" y="9" width="16" height="12" rx="1"/><path d="M7 9V3h10v6"/><line x1="8" y1="13" x2="16" y2="13"/><line x1="8" y1="17" x2="16" y2="17"/></svg>
        </li>
        <li>hello@ladle.com
          <svg class="icon" viewBox="0 0 24 24"><rect x="2.5" y="5" width="19" height="14" rx="1"/><path d="M3 6l9 7 9-7"/></svg>
        </li>
        <li>hello@ladle.com
          <svg class="icon" viewBox="0 0 24 24"><circle cx="12" cy="12" r="9.5"/><ellipse cx="12" cy="12" rx="4" ry="9.5"/><line x1="2.5" y1="12" x2="21.5" y2="12"/></svg>
        </li>
        <li class="web">www.gildedladlebakes.com</li>
      </ul>
    </div>
  </section>
</main>
</body>
</html>
```